New Business Card Design Project

Use the flyer uploaded and website www.brightoakbuilders.com for inspiration.
List Our Services on Backside of business cards
Marcus Delling
Harborline Builders Inc.
Licensed General Contractors
858-471-6093

Contact Information for Business Card

Use the flyer uploaded and website www.brightoakbuilders.com for inspiration. List Our Services on Backside of business cards Marcus Delling Harborline Builders Inc. Licensed General Contractors 858-471-6093

```html
<!DOCTYPE html>
<html lang="en">
<head>
<meta charset="utf-8">
<title>Harborline Builders – Business Cards</title>
<link href="https://fonts.googleapis.com/css2?family=Cormorant+Garamond:wght@400;500&family=Open+Sans:ital,wght@0,400;0,600;0,700;1,700&display=swap" rel="stylesheet">
<style>
  :root {
    --bg-center: #7a7b7f;
    --bg-edge: #4f5054;
    --card-dark: #141414;
    --card-light: #ffffff;
    --ink-light: #f2f2f2;
    --ink-dark: #1c1c1c;
    --accent-blue: #2f6fc4;
    --accent-red: #e0262b;
    --muted: #cfcfcf;
    --divider: #9a9a9a;
  }
  * { margin: 0; padding: 0; box-sizing: border-box; }
  html, body { width: 1200px; height: 781px; overflow: hidden; }
  body {
    background: radial-gradient(ellipse at 50% 40%, var(--bg-center), var(--bg-edge));
    font-family: "Open Sans", sans-serif;
    position: relative;
  }
  .card {
    position: absolute;
    top: 242px;
    width: 520px;
    height: 297px;
    border-radius: 18px;
    box-shadow: 0 14px 30px rgba(0,0,0,0.35);
    overflow: hidden;
  }
  .brand {
    font-family: "Cormorant Garamond", serif;
    font-weight: 400;
    white-space: nowrap;
    display: flex;
    align-items: center;
    gap: 10px;
  }
  .brand-dot { width: 9px; height: 9px; border-radius: 50%; display: inline-block; flex: none; }

  /* Front */
  .card-front { left: 50px; background: var(--card-dark); color: var(--ink-light); }
  .card-front .brand {
    position: absolute; top: 62px; left: 170px;
    font-size: 24px; letter-spacing: 1.5px; color: var(--ink-light);
  }
  .card-front .brand-dot { background: var(--ink-light); }
  .person { position: absolute; left: 24px; top: 180px; width: 206px; text-align: right; }
  .person-name {
    font-family: "Cormorant Garamond", serif;
    font-weight: 500;
    font-size: 21px;
    color: var(--accent-blue);
    letter-spacing: 0.5px;
    white-space: nowrap;
  }
  .person-title { font-size: 12px; color: var(--muted); margin-top: 2px; }
  .divider { position: absolute; left: 246px; top: 170px; width: 1px; height: 82px; background: var(--divider); }
  .contacts { position: absolute; left: 264px; top: 172px; list-style: none; }
  .contacts li { display: flex; align-items: center; gap: 9px; font-size: 13px; line-height: 26px; color: var(--ink-light); white-space: nowrap; }
  .contacts svg { width: 13px; height: 13px; flex: none; }
  .icon-fill { fill: var(--accent-red); }
  .icon-line { fill: none; stroke: var(--accent-red); stroke-width: 2.4; }

  /* Back */
  .card-back { left: 630px; background: var(--card-light); color: var(--ink-dark); }
  .card-back .brand {
    position: absolute; top: 96px; left: 34px;
    font-size: 26px; line-height: 28px; letter-spacing: 1.5px; color: var(--ink-dark);
  }
  .card-back .brand-dot { background: var(--ink-dark); }
  .services { position: absolute; left: 282px; top: 54px; width: 220px; }
  .guarantee {
    font-weight: 700; font-style: italic; font-size: 13px; line-height: 16px;
    color: var(--accent-red); text-transform: uppercase;
  }
  .specializing {
    margin-top: 4px; background: var(--accent-blue); color: #fff;
    font-size: 11.5px; font-weight: 600; padding: 2px 8px; display: inline-block; width: 160px;
    text-transform: uppercase;
  }
  .service-list { list-style: none; margin-top: 6px; }
  .service-list li { display: flex; align-items: center; gap: 6px; font-size: 11.5px; line-height: 17px; white-space: nowrap; }
  .tick { width: 11px; height: 10px; flex: none; }
  .tick rect { fill: none; stroke: var(--accent-red); stroke-width: 1.2; }
  .tick path { fill: none; stroke: var(--accent-red); stroke-width: 1.8; }
</style>
</head>
<body>
  <section class="card card-front" aria-label="Business card front">
    <div class="brand"><span class="brand-dot"></span>HARBORLINE BUILDERS</div>
    <div class="person">
      <div class="person-name">MARCUS DELLING</div>
      <div class="person-title">Director</div>
    </div>
    <div class="divider"></div>
    <ul class="contacts">
      <li><svg viewBox="0 0 24 24"><path class="icon-fill" d="M6.6 10.8a15 15 0 0 0 6.6 6.6l2.2-2.2c.3-.3.7-.4 1-.2 1.1.4 2.3.6 3.6.6.6 0 1 .4 1 1V20c0 .6-.4 1-1 1A17 17 0 0 1 3 4c0-.6.4-1 1-1h3.5c.6 0 1 .4 1 1 0 1.3.2 2.5.6 3.6.1.3 0 .7-.2 1z"/></svg>858-471-6093</li>
      <li><svg viewBox="0 0 24 24"><rect class="icon-line" x="2" y="5" width="20" height="14"/><path class="icon-line" d="M2 5l10 8 10-8"/></svg>md@brightoakbuilders.com</li>
      <li><svg viewBox="0 0 24 24"><circle class="icon-line" cx="12" cy="12" r="9.5"/><path class="icon-line" d="M2.5 12h19M12 2.5c-4 5-4 14 0 19M12 2.5c4 5 4 14 0 19"/></svg>www.brightoakbuilders.com</li>
    </ul>
  </section>

  <section class="card card-back" aria-label="Business card back">
    <div class="brand"><span class="brand-dot"></span><span>HARBORLINE<br>BUILDERS</span></div>
    <div class="services">
      <p class="guarantee">Our services are<br>100% guaranteed</p>
      <p class="specializing">Specializing in:</p>
      <ul class="service-list">
        <li><svg class="tick" viewBox="0 0 11 10"><rect x="0.6" y="2" width="7.5" height="7.4"/><path d="M2 5l2 2.5L10 1"/></svg>Remodel: Kitchen &amp; Bath</li>
        <li><svg class="tick" viewBox="0 0 11 10"><rect x="0.6" y="2" width="7.5" height="7.4"/><path d="M2 5l2 2.5L10 1"/></svg>Painting: Interior &amp; Exterior</li>
        <li><svg class="tick" viewBox="0 0 11 10"><rect x="0.6" y="2" width="7.5" height="7.4"/><path d="M2 5l2 2.5L10 1"/></svg>Flooring: Carpet, Vinyl, Wood</li>
        <li><svg class="tick" viewBox="0 0 11 10"><rect x="0.6" y="2" width="7.5" height="7.4"/><path d="M2 5l2 2.5L10 1"/></svg>Window &amp; Door Replacement</li>
        <li><svg class="tick" viewBox="0 0 11 10"><rect x="0.6" y="2" width="7.5" height="7.4"/><path d="M2 5l2 2.5L10 1"/></svg>Plumbing: Repairs &amp; Upgrades</li>
        <li><svg class="tick" viewBox="0 0 11 10"><rect x="0.6" y="2" width="7.5" height="7.4"/><path d="M2 5l2 2.5L10 1"/></svg>Energy-Efficient Upgrades</li>
        <li><svg class="tick" viewBox="0 0 11 10"><rect x="0.6" y="2" width="7.5" height="7.4"/><path d="M2 5l2 2.5L10 1"/></svg>Deck &amp; Patio Construction</li>
        <li><svg class="tick" viewBox="0 0 11 10"><rect x="0.6" y="2" width="7.5" height="7.4"/><path d="M2 5l2 2.5L10 1"/></svg>Water &amp; Mold Damage</li>
        <li><svg class="tick" viewBox="0 0 11 10"><rect x="0.6" y="2" width="7.5" height="7.4"/><path d="M2 5l2 2.5L10 1"/></svg>Garage Renovation</li>
      </ul>
    </div>
  </section>
</body>
</html>
```